Business Card & Stationary
Powder Coating Company
Project: Business Card & Stationary
Business Card & Stationary - Miscellaneous
Creative Brief
Professional
Laurent Bexhold
Owner / Operator
4172 Ave K 1/2
nullemail@tarrowfinishline.com
www.tarrowfinishline.com
Should list our services, which include Powder Coating, Ceramic Coating and Abrasive Blasting

```html
<!DOCTYPE html>
<html lang="en">
<head>
<meta charset="utf-8">
<title>Tarrow Finish Line – Business Cards</title>
<link href="https://fonts.googleapis.com/css2?family=Arimo:wght@400;700&display=swap" rel="stylesheet">
<style>
  :root {
    --canvas: #ececec;
    --red: #c8101b;
    --white: #ffffff;
    --black: #050505;
    --ink: #2a2a2a;
    --border: #bdbdbd;
  }
  * { margin: 0; padding: 0; box-sizing: border-box; }
  html, body {
    width: 1200px; height: 713px; overflow: hidden;
    background: var(--canvas);
    font-family: "Arimo", Arial, sans-serif;
  }
  .sheet { position: relative; width: 1200px; height: 713px; }
  .card {
    position: absolute; width: 570px; height: 324px; overflow: hidden;
    border: 1px solid var(--border);
  }
  .card--front { left: 19px; top: 19px; background: var(--white); }
  .card--red { left: 611px; top: 19px; background: var(--red); }
  .card--white { left: 19px; top: 367px; background: var(--white); }
  .card--black { left: 611px; top: 367px; background: var(--black); }

  .front-band { position: absolute; inset: 0; }

  .brand-name {
    position: absolute; font-weight: 700; font-size: 34px; letter-spacing: -0.5px;
    white-space: nowrap;
  }
  .card--front .brand-name { left: 26px; top: 62px; color: var(--red); font-size: 30px; }
  .brand-name--center { left: 0; right: 0; top: 120px; text-align: center; }
  .card--red .brand-name { color: var(--white); }
  .card--white .brand-name { color: var(--red); }
  .card--black .brand-name { color: var(--white); }

  .person-name {
    position: absolute; left: 26px; top: 192px;
    color: var(--red); font-size: 20px;
  }
  .person-role {
    position: absolute; left: 26px; top: 224px;
    color: var(--ink); font-size: 15px;
  }
  .contact {
    position: absolute; right: 14px; top: 196px;
    text-align: right; color: var(--ink); font-size: 13.5px; line-height: 21px;
    list-style: none;
  }
  .services {
    position: absolute; left: 0; right: 0; top: 216px;
    text-align: center; font-size: 15.5px; line-height: 26px;
  }
  .card--red .services, .card--black .services { color: var(--white); }
  .card--white .services { color: var(--ink); }
</style>
</head>
<body>
<main class="sheet">
  <section class="card card--front">
    <svg class="front-band" width="570" height="324" viewBox="0 0 570 324" aria-hidden="true">
      <path d="M220 0 C300 80 430 150 570 178 L570 0 Z" fill="var(--red)"/>
    </svg>
    <div class="brand-name">Tarrow Finish Line</div>
    <p class="person-name">Laurent Bexhold</p>
    <p class="person-role">Owner / Operator</p>
    <ul class="contact">
      <li>4172 Ave K 1/2</li>
      <li>Phone: (318) 555-2046</li>
      <li>Fax: (318) 555-7390</li>
      <li>Email: nullemail@tarrowfinishline.com</li>
      <li>www.tarrowfinishline.com</li>
    </ul>
  </section>

  <section class="card card--red">
    <div class="brand-name brand-name--center">Tarrow Finish Line</div>
    <p class="services">which include Powder Coating,<br>Ceramic Coating and Abrasive Blasting</p>
  </section>

  <section class="card card--white">
    <div class="brand-name brand-name--center">Tarrow Finish Line</div>
    <p class="services">which include Powder Coating,<br>Ceramic Coating and Abrasive Blasting</p>
  </section>

  <section class="card card--black">
    <div class="brand-name brand-name--center">Tarrow Finish Line</div>
    <p class="services">which include Powder Coating,<br>Ceramic Coating and Abrasive Blasting</p>
  </section>
</main>
</body>
</html>
```